Schlichtes Design für Malerbetrieb
Zielgruppe
Wir sind ein mittelgroßer Malerbetrieb in München mit umfangreichem Leistungsspektrum.
Unsere Hauptleistungen sind: Fassadenrenovierung, Altbausanierung, Betoninstandsetzung, Balkonabdichtung (kein Neubau!).
Unsere Zielgruppen sind: Hausverwaltungen, Firmen und Privatpersonen.
Unsere Kunden schätzen: Konstruktive Organisation und Planung im Vorfeld, Zuverlässigkeit, saubere Arbeitsweise, dauerhafte Balkonabdichtungen.
Aufgabenstellung
Wir möchten eine langlebige, stilvolle, minimalistische Homepage.
Wir möchten von der bestehenden Homepage nur die Schriftart für unseren Firmennamen (Century Gothic) und wenn möglich (nicht zwingend), irgendwo das florale Muster einbauen. Corporate-Design haben wir nicht.
Farbtöne: Firmennamen Orange (hellorange bis erdiges Orange möglich, da sind wir nicht fixiert) , einen dunklen Hintergrundfarbton (Petrol-Blaugrau ?) mit gelbem (neon bis senfgelb) Akzent (Linien), Blumenmuster weiß, grau.
Dies sind nur unsere Ideen. Wir sind aber auch absolut offen für eure Profi-Ideen.
Wir möchten uns von den unzähligen langweiligen 'Pinselseiten mit veralteten Bilder' unserer Kollegen interessant und mit Stil abheben.
Eher nach dem Motto 'weniger ist mehr'.
Einen positiven, sympathischen Eindruck geben und unsere Leistungen in den Vordergrund bringen.
Da wir viele Stammkunden haben, betreiben wir kein Social-Media und möchten dies vorerst auch nicht tun.
Die Seite wird in den nächsten Jahren nicht verändert, höchstens die Bilder aktualisiert.
Die Texte haben wir alle selbst entworfen und möchten wir so übernehmen.
Die Galerien sollen unkompliziert anzuschauen sein.
Uns gefällt die Struktur und Schlichtheit von https://vaartmolen.nl/ oder Timbra.de gut und wir mögen Vintage-Grafiken gerne.
Einerseits darf die Seite geradlinig, andererseits aber auch rund und floral wirken.

```html
<!DOCTYPE html>
<html lang="de">
<head>
<meta charset="utf-8">
<title>kolbrit Malerarbeiten</title>
<link rel="stylesheet" href="https://fonts.googleapis.com/css2?family=Questrial&family=Fira+Sans+Condensed:wght@400&display=swap">
<style>
  :root {
    --charcoal: #3c3b3d;
    --pattern-ground: #3a393b;
    --petrol: #043f52;
    --amber: #f7b232;
    --stone: #b2b3b5;
    --mist: #a9acae;
    --white: #ffffff;
  }
  * { margin: 0; padding: 0; box-sizing: border-box; }
  html, body { width: 1200px; height: 900px; overflow: hidden; background: var(--charcoal); }
  .page { position: relative; width: 1200px; height: 900px; }

  .site-header { position: absolute; top: 0; left: 0; width: 1200px; height: 125px; background: var(--charcoal); }
  .header-brand {
    position: absolute; top: 16px; right: 46px;
    font-family: "Questrial", sans-serif; font-size: 48px; color: var(--amber); letter-spacing: 1px;
  }
  .main-nav {
    position: absolute; top: 86px; left: 47px; width: 1102px;
    display: flex; justify-content: space-between;
    font-family: "Fira Sans Condensed", sans-serif; font-size: 23px; color: var(--white);
  }

  .hero { position: absolute; top: 125px; left: 0; width: 1200px; height: 716px; }
  .hero svg { display: block; }

  .hero-brand {
    position: absolute; left: 190px; top: 255px; width: 350px; text-align: center;
  }
  .brand-dot { width: 30px; height: 30px; border-radius: 50%; background: var(--mist); margin: 0 auto 22px; }
  .brand-name { font-family: "Questrial", sans-serif; font-size: 72px; line-height: 1; color: var(--amber); }
  .brand-tag {
    font-family: "Questrial", sans-serif; font-size: 21px; color: var(--mist);
    letter-spacing: 4px; margin-top: 8px;
  }

  .site-footer { position: absolute; bottom: 0; left: 0; width: 1200px; height: 59px; background: var(--charcoal); }
  .footer-nav {
    position: absolute; right: 17px; top: 13px; display: flex; gap: 24px;
    font-family: "Fira Sans Condensed", sans-serif; font-size: 24px; color: var(--white);
  }
</style>
</head>
<body>
<div class="page">
  <header class="site-header">
    <div class="header-brand">kolbrit</div>
    <nav class="main-nav">
      <span>malerarbeiten</span><span>betoninstandsetzung</span><span>balkonabdichtung</span>
      <span>farbgestaltung</span><span>wärmedämmung</span><span>ausbildung</span><span>portrait</span>
    </nav>
  </header>

  <section class="hero">
    <svg width="1200" height="716" viewBox="0 107 1024 611" preserveAspectRatio="none">
      <rect x="0" y="107" width="1024" height="611" fill="var(--pattern-ground)" role="img" aria-label="Dezentes florales Damastmuster in Grautönen"/>
      <polygon points="0,107 220,107 728,355 275,582 0,448" fill="var(--petrol)"/>
      <polygon points="0,448 550,718 0,718" fill="var(--stone)"/>
      <polygon points="1024,212 1024,715 510,463" fill="var(--amber)"/>
    </svg>
    <div class="hero-brand">
      <div class="brand-dot"></div>
      <div class="brand-name">kolbrit</div>
      <div class="brand-tag">MALERARBEITEN</div>
    </div>
  </section>

  <footer class="site-footer">
    <nav class="footer-nav"><span>Kontakt</span><span>Impressum</span><span>Datenschutz</span></nav>
  </footer>
</div>
</body>
</html>
```